Brindlemark Group information card

We need a 5x7 two-sided card to hand out at open houses and provide to our charitable partners for distribution. We are a local real estate group looking to add a "give back" component to our business. We are located in a coastal community and would like to incorporate that feel into our design. We are giving clients who use us the ability to designate 1 out of the 10 charitable organizations we partner with - and we will make a donation to that organization.

We included the 10 partner logos below - we envision them pretty small. Also included 2 photos of the "Brindlemark" and our logo. Have fun.
Updates

Target Market(s)

home buyers & sellers

Industry/Entity Type

Real Estate

Font styles to use
Serif
Sans Serif

Colors

Designer to choose colors to be used in the design.

Requirements
Must have
• slogan & tagline - see attached text file
• Brindlemark photo
Nice to have
• partner logos - small - maybe in circles?

```html
<!DOCTYPE html>
<html lang="en">
<head>
<meta charset="utf-8">
<title>Brindlemark Group – Give Back Card</title>
<link rel="stylesheet" href="https://fonts.googleapis.com/css2?family=Ubuntu:wght@400;500&family=Open+Sans:wght@400&display=swap">
<style>
  :root {
    --stage: #9c9c9c;
    --brand-blue: #5b85c6;
    --deep-blue: #3c5d93;
    --navy-veil: rgba(52, 66, 104, 0.82);
    --ink: #1f1f1f;
    --link: #4a78c0;
    --white: #ffffff;
    --panel: rgba(255, 255, 255, 0.93);
    --footer-veil: rgba(93, 125, 185, 0.86);
  }
  * { box-sizing: border-box; margin: 0; padding: 0; }
  html, body { width: 1200px; height: 800px; overflow: hidden; }
  body { background: var(--stage); position: relative; font-family: "Open Sans", sans-serif; }

  .card { position: absolute; overflow: hidden; background: var(--white); }
  .card--front { left: 39px; top: 8px; width: 554px; height: 775px; }
  .card--back  { left: 619px; top: 8px; width: 553px; height: 773px; }

  /* Front */
  .front-photo {
    position: absolute; left: 0; top: 0; width: 554px; height: 464px;
    background: linear-gradient(180deg, #c87a86 0%, #e9826a 30%, #d9867c 48%, #8e5f6e 62%, #3e3848 76%, #262a35 100%);
  }
  .brand-mark {
    position: absolute; color: var(--white); font-family: "Ubuntu", sans-serif; font-weight: 500;
    text-align: center; line-height: 1;
  }
  .front-brand { right: 30px; top: 80px; width: 240px; }
  .front-brand .brand-name { font-size: 38px; }
  .front-brand .brand-sub { font-size: 28px; margin-top: 8px; }

  .slogan-band { position: absolute; left: 0; top: 464px; width: 554px; height: 110px; }
  .slogan-box {
    position: absolute; left: 0; top: 0; width: 340px; height: 110px; background: var(--brand-blue);
    color: var(--white); font-family: "Ubuntu", sans-serif; font-size: 38px; line-height: 40px;
    padding: 20px 0 0 24px; letter-spacing: 0.3px;
  }
  .tagline-box {
    position: absolute; left: 340px; top: 0; width: 214px; height: 110px;
    background: linear-gradient(180deg, #4a5575, #2f3953); color: var(--white);
    font-family: "Ubuntu", sans-serif; font-size: 18px; line-height: 27px; text-align: center; padding-top: 30px;
  }
  .front-body {
    position: absolute; left: 34px; top: 596px; width: 486px; color: var(--ink);
    font-size: 14.5px; line-height: 21.5px; text-align: justify; text-align-last: center;
  }
  .web-icon {
    position: absolute; left: 263px; top: 702px; width: 32px; height: 32px; border-radius: 50%;
    background: var(--brand-blue); color: var(--white); font-size: 10px; line-height: 32px; text-align: center;
  }
  .web-url { position: absolute; left: 0; width: 554px; top: 740px; text-align: center; color: var(--link); font-size: 12.5px; }

  /* Back */
  .back-photo {
    position: absolute; inset: 0;
    background: linear-gradient(180deg, #eef3f9 0%, #d2e0f0 14%, #a9c3e6 24%, #c8d9ee 40%, #f1f4f7 52%, #dde6ee 60%,
      #7fa5c4 63%, #9aa79a 70%, #8f9a82 80%, #7a8a6a 88%, #9c5c52 96%, #a0524a 100%);
  }
  .back-brand { left: 30px; top: 26px; width: 160px; color: var(--deep-blue); }
  .back-brand .brand-name { font-size: 27px; }
  .back-brand .brand-sub { font-size: 21px; margin-top: 6px; }
  .back-headline {
    position: absolute; right: 24px; top: 16px; text-align: right; color: var(--deep-blue);
    font-family: "Ubuntu", sans-serif; font-weight: 500; font-size: 46px; line-height: 52px; letter-spacing: 1px;
  }
  .give-panel { position: absolute; left: 0; top: 122px; width: 553px; height: 202px; }
  .give-text {
    position: absolute; right: 28px; top: 141px; width: 300px; text-align: right; color: #2e3440;
    font-size: 10.5px; line-height: 14.8px;
  }
  .give-tell { position: absolute; right: 28px; top: 287px; color: var(--deep-blue); font-family: "Ubuntu", sans-serif; font-size: 15.5px; }
  .partners { position: absolute; left: 0; top: 0; width: 553px; height: 773px; pointer-events: none; }
  .back-closer {
    position: absolute; right: 20px; top: 338px; text-align: right; color: var(--deep-blue);
    font-family: "Ubuntu", sans-serif; font-weight: 500; font-size: 23px; line-height: 24px;
  }
  .contact-bar {
    position: absolute; left: 0; top: 712px; width: 553px; height: 50px; background: var(--footer-veil); color: var(--white);
    font-family: "Ubuntu", sans-serif;
  }
  .contact-icon { position: absolute; left: 100px; top: 8px; }
  .contact { position: absolute; top: 6px; }
  .contact--one { left: 146px; }
  .contact--two { left: 302px; }
  .contact-name { font-size: 20px; line-height: 22px; letter-spacing: -0.3px; }
  .contact-mail { font-family: "Open Sans", sans-serif; font-size: 10.5px; line-height: 16px; }
  .contact-divider { position: absolute; left: 286px; top: 10px; width: 2px; height: 30px; background: var(--white); }
</style>
</head>
<body>

<section class="card card--front">
  <div class="front-photo" role="img" aria-label="Photo of the coastal town at sunset, with a pink and orange sky over the bay and pier"></div>
  <div class="brand-mark front-brand">
    <div class="brand-name">Brindlemark</div>
    <div class="brand-sub">Group</div>
  </div>
  <div class="slogan-band">
    <h1 class="slogan-box" style="font-weight:400">CHANGE HOMES,<br>CHANGE LIVES</h1>
    <p class="tagline-box">Changing the World<br>One Home at a Time</p>
  </div>
  <p class="front-body">Because we value generosity and desire to make a difference in our community and world, for every home bought or sold through us, we will make a contribution to one of our amazing partner who are helping to change the world.</p>
  <div class="web-icon">www</div>
  <p class="web-url">www.brindlemarkgroup.com</p>
</section>

<section class="card card--back">
  <div class="back-photo" role="img" aria-label="Photo of a bright sky with clouds above the coastal town, the beach curve and pier, with red flowers in the foreground"></div>
  <div class="brand-mark back-brand">
    <div class="brand-name">Brindlemark</div>
    <div class="brand-sub">Group</div>
  </div>
  <h2 class="back-headline">WE LIVE HERE.<br>WE GIVE HERE.</h2>

  <svg class="partners" width="553" height="773" viewBox="0 0 553 773" aria-hidden="true">
    <polygon points="0,122 197,122 197,122 0,122" fill="none"/>
    <polygon points="197,122 553,122 553,323 315,323" fill="#ffffff" fill-opacity="0.93"/>
    <g fill="#ffffff" stroke="#d5dbe4" stroke-width="1">
      <circle cx="47" cy="174" r="20" fill="#9a8f9c"/>
      <circle cx="114" cy="174" r="20" fill="#d8272d"/>
      <circle cx="180" cy="174" r="20"/>
      <circle cx="47" cy="234" r="20" fill="#4f6a3e"/>
      <circle cx="114" cy="234" r="20"/>
      <circle cx="180" cy="234" r="20"/>
      <circle cx="47" cy="296" r="20" fill="#6b5142"/>
      <circle cx="114" cy="296" r="20" fill="#e48bbf"/>
      <circle cx="180" cy="296" r="20" fill="#2a2a2a"/>
      <circle cx="246" cy="296" r="20" fill="#111111"/>
    </g>
  </svg>

  <p class="give-text">We give because we value generosity and believe we have been blessed to be a blessing. We believe that together we can changethe world one home at time. You have our guarantee of personal service and no additional costs. The donations come out of our commission, not your pocket. You get to designate which of our amazing partner organizations you would like us to contribute to on behalf of your transaction. When you are ready to buy or sell, please consider giving us a call</p>
  <p class="give-tell">Tell a friend about us too.</p>

  <h3 class="back-closer" style="font-weight:500">TOGETHER, WE CAN<br>MAKE THE WORLD<br>A BETTER PLACE.</h3>

  <footer class="contact-bar">
    <svg class="contact-icon" width="34" height="34" viewBox="0 0 34 34" aria-hidden="true">
      <circle cx="17" cy="17" r="16" fill="#ffffff"/>
      <rect x="9" y="11.5" width="16" height="11" rx="1" fill="none" stroke="#5b85c6" stroke-width="1.6"/>
      <polyline points="9.5,12.5 17,18 24.5,12.5" fill="none" stroke="#5b85c6" stroke-width="1.6"/>
    </svg>
    <div class="contact contact--one">
      <div class="contact-name">EVAN MARLOW</div>
      <div class="contact-mail">evan@brindlemarkgroup.com</div>
    </div>
    <div class="contact-divider"></div>
    <div class="contact contact--two">
      <div class="contact-name">JOAN MARLOW</div>
      <div class="contact-mail">joan@brindlemarkgroup.com</div>
    </div>
  </footer>
</section>

</body>
</html>
```